Single-sided business card for restaurant velmora with new logo made on this site

Business card options with new logo including restaurant name, address, phone number and website. This business card is single-sided only and will be presented at the hostess desk for clients to take. I would like to see options based on a cream card background, a white card background, a yellow card background and a burgundy colored background. It needs to be elegant and traditional.

Target Market(s)

local and international crowd

Industry/Entity Type

restaurant

Contact Information for Business Card

address, website and phone number

Font styles to use
Serif

Colors
EE7325
F08F49
F5BC92
FAE3D3
FDF4ED

Requirements
Must have
• new logo, address, phone number, website
Should not have
• more than three colors

```html
<!DOCTYPE html>
<html lang="en">
<head>
<meta charset="utf-8">
<title>Velmora — Business Card</title>
<link rel="stylesheet" href="https://fonts.googleapis.com/css2?family=EB+Garamond:wght@400;600&display=swap">
<style>
  :root {
    --page: #d9d9d9;
    --card: #fdf4ed;
    --brown: #3f2024;
    --accent: #ee7325;
    --accent-soft: #f08f49;
    --ink: #2a1a1c;
    --text: #3a2a2c;
    --web-light: #fae3d3;
  }
  * { margin: 0; padding: 0; box-sizing: border-box; }
  html, body { width: 1156px; height: 1200px; overflow: hidden; background: var(--page); }
  body { font-family: "EB Garamond", serif; color: var(--text); }

  .card {
    position: absolute;
    left: 108px;
    width: 940px;
    height: 537px;
    background: var(--card);
    border-radius: 38px;
    overflow: hidden;
    box-shadow: 0 4px 10px rgba(0,0,0,0.25);
  }
  .card--brown-band { top: 42px; }
  .card--accent-band { top: 621px; }

  .card__bands { position: absolute; left: 0; top: 0; width: 940px; height: 537px; }

  .brand { position: absolute; left: 100px; top: 108px; width: 354px; text-align: center; }
  .brand__square { display: block; width: 172px; height: 172px; margin: 0 auto; background: var(--accent); }
  .brand__name {
    margin-top: 24px;
    font-size: 52px;
    font-weight: 600;
    letter-spacing: 8px;
    color: var(--brown);
    line-height: 1;
  }

  .contact { position: absolute; left: 505px; top: 98px; }
  .contact__name { font-size: 40px; font-weight: 600; color: var(--brown); line-height: 1.1; }
  .contact__role { font-size: 26px; color: var(--accent); margin-top: 4px; line-height: 1.1; }
  .contact__address { margin-top: 38px; font-size: 26px; line-height: 34px; padding-left: 6px; }
  .contact__line { display: flex; align-items: center; font-size: 26px; line-height: 38px; padding-left: 12px; }
  .contact__icon { width: 20px; height: 20px; margin-right: 16px; fill: var(--brown); }

  .card__web {
    position: absolute;
    right: 130px;
    bottom: 14px;
    font-size: 26px;
    line-height: 1;
  }
  .card--brown-band .card__web { color: var(--web-light); }
  .card--accent-band .card__web { color: var(--ink); }
</style>
</head>
<body>

<section class="card card--brown-band">
  <svg class="card__bands" viewBox="0 0 940 537" aria-hidden="true">
    <path d="M0,537 C120,505 300,482 700,470 L600,472 C380,488 220,510 110,537 Z" fill="var(--accent)"/>
    <path d="M150,537 C380,490 640,468 940,468 L940,537 Z" fill="var(--brown)"/>
  </svg>
  <div class="brand">
    <span class="brand__square"></span>
    <div class="brand__name">VELMORA</div>
  </div>
  <div class="contact">
    <div class="contact__name">Martin Alcott</div>
    <div class="contact__role">General Manager</div>
    <div class="contact__address">Jazmín 418<br>Playa Serena<br>Oaxaca CP 70310</div>
    <div class="contact__line">
      <svg class="contact__icon" viewBox="0 0 24 24"><path d="M6.6 10.8a15 15 0 0 0 6.6 6.6l2.2-2.2a1 1 0 0 1 1-.25 11.4 11.4 0 0 0 3.6.57 1 1 0 0 1 1 1V20a1 1 0 0 1-1 1A17 17 0 0 1 3 4a1 1 0 0 1 1-1h3.5a1 1 0 0 1 1 1 11.4 11.4 0 0 0 .57 3.6 1 1 0 0 1-.25 1z"/></svg>
      555-204-7381
    </div>
    <div class="contact__line">
      <svg class="contact__icon" viewBox="0 0 24 24"><path d="M2 5h20v14H2z M3.5 6.5 12 13l8.5-6.5" fill="var(--brown)" stroke="var(--card)" stroke-width="1.5"/></svg>
      martin@velmora.com.mx
    </div>
  </div>
  <div class="card__web">www.velmora.com.mx</div>
</section>

<section class="card card--accent-band">
  <svg class="card__bands" viewBox="0 0 940 537" aria-hidden="true">
    <path d="M20,537 C200,498 420,478 690,472 L600,474 C400,488 220,512 120,537 Z" fill="var(--brown)"/>
    <path d="M170,537 C400,492 660,472 940,472 L940,537 Z" fill="var(--accent)"/>
  </svg>
  <div class="brand">
    <span class="brand__square"></span>
    <div class="brand__name">VELMORA</div>
  </div>
  <div class="contact">
    <div class="contact__name">Martin Alcott</div>
    <div class="contact__role">General Manager</div>
    <div class="contact__address">Jazmín 418<br>Playa Serena<br>Oaxaca CP 70310</div>
    <div class="contact__line">
      <svg class="contact__icon" viewBox="0 0 24 24"><path d="M6.6 10.8a15 15 0 0 0 6.6 6.6l2.2-2.2a1 1 0 0 1 1-.25 11.4 11.4 0 0 0 3.6.57 1 1 0 0 1 1 1V20a1 1 0 0 1-1 1A17 17 0 0 1 3 4a1 1 0 0 1 1-1h3.5a1 1 0 0 1 1 1 11.4 11.4 0 0 0 .57 3.6 1 1 0 0 1-.25 1z"/></svg>
      555-204-7381
    </div>
    <div class="contact__line">
      <svg class="contact__icon" viewBox="0 0 24 24"><path d="M2 5h20v14H2z M3.5 6.5 12 13l8.5-6.5" fill="var(--brown)" stroke="var(--card)" stroke-width="1.5"/></svg>
      martin@velmora.com.mx
    </div>
  </div>
  <div class="card__web">www.velmora.com.mx</div>
</section>

</body>
</html>
```